A New and modern Business Card for Tarwick Trade Solutions Ltd

New and modern Logo and Business Card Attached is the current logo/business card designCurrently the business is called "Tarwick & Co." or TTS Ltd for short. This is subject to change.This business specialises in Telecoms and Energy. We work with the major networks (QV, K7, etc) and also offer Energy Products saving clients money off their energy bills.These are business to business services.The current design incorporates a Pheonix, indicating rebirth, starting something new.We would like to maintain the Phoenix element but a newer modern style.We love colours in the logo 3 max.The aim of this is to be ultra slick and modern. I envisage Tarwick & Co. on one side of the card with long descriptions on the other side.Side 1:TTS Ltd/Logo?Side 2:TTS Ltd/Logo/Graphic?Brogan & Co.Name:Address:Phone:Email:The design is mostly flexible but must incorporate a Phoenix.For example "Tarwick & Co." with a block phoenix behind the text...up to you.

Industry/Entity Type

Telecommunications

Contact Information for Business Card

Tarwick & Co.
Address:
Name:
Phone:
Email:

Logo Text

Tarwick & Co.

Colors
33a6d7
0792cd
acd037
9bcb3c
f78f20
fece3e

Requirements
Must have
• Phoenix
• 3/4 colours max
• Blue representing Technology (wireless)
• Green for Eco Energy
• Orange for Phoenix
• White business card background
Should not have
• phoenix must not all be red/ orange fire, we are a technology service company and the phoenix colours must represent this. Fire is not representative of our company.

```html
<!DOCTYPE html>
<html lang="en">
<head>
<meta charset="utf-8">
<title>Tarwick Trade Solutions Ltd – Business Card</title>
<link rel="stylesheet" href="https://fonts.googleapis.com/css2?family=Cinzel:wght@500;600&family=Lato:wght@400&display=swap">
<style>
  :root {
    --stage: #5b5b5b;
    --card-white: #ffffff;
    --tech-blue: #0792cd;
    --tech-blue-light: #33a6d7;
    --eco-green: #9bcb3c;
    --phoenix-orange: #f78f20;
    --soft-orange: #fcd3a8;
    --text-light: #ffffff;
  }
  html, body {
    margin: 0;
    padding: 0;
    width: 1200px;
    height: 802px;
    overflow: hidden;
    background: var(--stage);
  }
  .canvas {
    position: relative;
    width: 1200px;
    height: 802px;
  }
  .card {
    position: absolute;
    top: 274px;
    width: 442px;
    height: 264px;
    background: var(--card-white);
    box-shadow: 0 3px 8px rgba(0,0,0,0.35);
    overflow: hidden;
  }
  .card--front { left: 136px; }
  .card--back { left: 624px; }
  .card svg { display: block; width: 100%; height: 100%; }
  .contact-name { font-family: "Cinzel", serif; font-weight: 600; font-size: 19px; fill: var(--text-light); letter-spacing: 0.3px; }
  .contact-role, .contact-line { font-family: "Lato", sans-serif; font-size: 15px; fill: var(--text-light); }
  .brand-name { text-anchor: middle; }
  .brand-name--main { font-family: "Cinzel", serif; font-weight: 500; font-size: 46px; fill: var(--tech-blue); }
  .brand-name--sub { font-family: "Lato", sans-serif; font-weight: 400; font-size: 13.5px; letter-spacing: 0.6px; fill: var(--eco-green); }
</style>
</head>
<body>
<main class="canvas">

  <section class="card card--front" aria-label="Card front with contact details">
    <svg viewBox="0 0 544 325" xmlns="http://www.w3.org/2000/svg">
      <defs>
        <radialGradient id="phoenixGlow" cx="0.6" cy="0.55" r="0.55">
          <stop offset="0" stop-color="#ffffff"/>
          <stop offset="0.55" stop-color="#fde3c6"/>
          <stop offset="1" stop-color="#f78f20" stop-opacity="0"/>
        </radialGradient>
      </defs>
      <rect class="front-green" width="544" height="325" fill="var(--eco-green)"/>
      <path class="front-swoosh" d="M193 0 H216 C250 130 370 250 490 325 H430 C330 260 230 140 193 0 Z" fill="#ffffff"/>
      <path class="front-blue" d="M0 0 H193 C225 140 320 260 430 325 H0 Z" fill="var(--tech-blue)"/>
      <path class="front-accent" d="M230 212 C290 270 360 305 420 325 H395 C330 300 270 260 230 212 Z" fill="#ffffff"/>
      <ellipse class="phoenix-decoration" role="img" aria-label="Large phoenix illustration in orange and white" cx="440" cy="200" rx="140" ry="150" fill="url(#phoenixGlow)"/>

      <text class="contact-name" x="30" y="179">DANIEL MORROW</text>
      <text class="contact-role" x="30" y="197">Managing Director</text>

      <g class="icon-phone" fill="#ffffff" transform="translate(29 211)">
        <path d="M1 3 C1 1 3 0 6 0 C9 0 11 1 11 3 L8 3 L8 2 C7 1.5 5 1.5 4 2 L4 3 Z"/>
        <rect x="2" y="4" width="8" height="5" rx="1"/>
      </g>
      <text class="contact-line" x="46" y="222">044-987 654 321</text>

      <g class="icon-mail" transform="translate(29 233)">
        <rect width="11" height="8" fill="#ffffff"/>
        <path d="M0 0 L5.5 4.5 L11 0" fill="none" stroke="var(--tech-blue)" stroke-width="1.2"/>
      </g>
      <text class="contact-line" x="46" y="242">hello@tarwickmail.com</text>

      <text class="contact-line" x="31" y="267">58, Harlow Quay Road,</text>
      <text class="contact-line" x="31" y="287">30917,Eastmere</text>
    </svg>
  </section>

  <section class="card card--back" aria-label="Card back with company name">
    <svg viewBox="0 0 544 325" xmlns="http://www.w3.org/2000/svg">
      <defs>
        <radialGradient id="faintGlow" cx="0.5" cy="0.5" r="0.5">
          <stop offset="0" stop-color="var(--soft-orange)" stop-opacity="0.3"/>
          <stop offset="1" stop-color="var(--soft-orange)" stop-opacity="0"/>
        </radialGradient>
      </defs>
      <rect width="544" height="325" fill="var(--card-white)"/>
      <ellipse class="faint-decoration" role="img" aria-label="Faint large phoenix watermark decoration" cx="115" cy="185" rx="130" ry="140" fill="url(#faintGlow)"/>
      <circle class="brand-dot" cx="274" cy="132" r="28" fill="var(--phoenix-orange)"/>
      <text class="brand-name brand-name--main" x="274" y="236">TARWICK</text>
      <text class="brand-name brand-name--sub" x="274" y="253">TRADE SOLUTIONS LIMITED</text>
    </svg>
  </section>

</main>
</body>
</html>
```